Velborix advertisement one page flyer design

We need a flyer design for our company to advertise what we offer, it only needs to be one sided, approx A5 in size.
Our logo: http://velborix-example.com/images/logo.png (I will provide in high-res later)
We offer, website design, development, bespoke applications. We would like to advertise that we can be hired for short term contracts for companies who need help with their work load.
Some of, but not limited to the systems we build are content management systems, e-commerce systems & event booking systems.
Our strap line is "We design, develop and deliver", a nice sleek redesign of the image on our website would be nice, but not required 100% - http://velborix-example.com/
Other details to put on the flyer:-
Email: hello@velborix-example.com
Tel: 01632 960 417
Address: Velborix Ltd, Crest Suites, Dunmoor Road, Cheltenham, GL53 4QT
We welcome any other ideas.

```html
<!DOCTYPE html>
<html lang="en">
<head>
<meta charset="utf-8">
<title>Velborix Flyer</title>
<link rel="stylesheet" href="https://fonts.googleapis.com/css2?family=Kalam:wght@400;700&family=Russo+One&family=Francois+One&family=Arimo:wght@400;700&display=swap">
<style>
  :root {
    --page-bg: #ece8e2;
    --hero-deep: #8a2a08;
    --hero-mid: #d9601c;
    --hero-light: #f6a24a;
    --stripe-orange: #e0622a;
    --wave-grey: #5b5656;
    --panel-orange: #f19a4b;
    --panel-light: #e4e4e4;
    --panel-grey: #c6c6c6;
    --accent: #ea7a26;
    --ink: #2b2b2b;
    --ink-grey: #555152;
    --white: #ffffff;
  }
  * { margin: 0; padding: 0; box-sizing: border-box; }
  html, body { width: 847px; height: 1200px; overflow: hidden; background: var(--page-bg); }
  .canvas { position: relative; width: 847px; height: 1200px; }
  .flyer { position: absolute; left: 30px; top: 40px; width: 788px; height: 1120px; overflow: hidden; }
  .flyer-shapes { position: absolute; inset: 0; }
  .abs { position: absolute; }
  .hero-visual { position: absolute; left: 0; top: 0; width: 788px; height: 540px;
    background: radial-gradient(ellipse at 68% 35%, var(--hero-light) 0%, var(--hero-mid) 45%, var(--hero-deep) 100%); }
  .brand-name { left: 30px; top: 58px; font-family: "Russo One", sans-serif; font-size: 76px;
    color: var(--white); line-height: 1; display: flex; align-items: center; gap: 14px; }
  .brand-dot { width: 26px; height: 26px; border-radius: 50%; background: var(--white); }
  .offer-text { left: 27px; font-family: "Kalam", cursive; font-size: 25px; line-height: 35px; color: var(--white); }
  .offer-services { top: 180px; }
  .offer-contract { top: 312px; }
  .section-title { font-family: "Kalam", cursive; color: var(--ink); line-height: 1; }
  .how-title { left: 27px; top: 575px; font-size: 38px; }
  .solutions-title { left: 480px; top: 574px; font-size: 27px; }
  .step { left: 50px; display: flex; align-items: center; gap: 22px; }
  .step-icon { width: 84px; height: 84px; border-radius: 50% 50% 50% 8px; background: var(--accent); }
  .step-word { font-family: "Russo One", sans-serif; font-size: 64px; color: var(--ink-grey); line-height: 1; }
  .step-word small { font-size: 24px; display: block; color: var(--ink-grey); }
  .solutions { left: 480px; top: 618px; list-style: none; }
  .solution { display: flex; align-items: center; gap: 10px; height: 58px; }
  .solution-icon { width: 52px; height: 52px; border-radius: 50% 50% 50% 6px; background: var(--accent);
    border: 3px solid var(--white); }
  .solution-name { font-family: "Francois One", sans-serif; font-size: 19px; color: var(--ink); letter-spacing: .3px; }
  .cta { left: 27px; top: 1062px; font-family: "Kalam", cursive; font-weight: 700; font-size: 30px; color: var(--accent); }
  .contact { left: 380px; top: 1015px; font-family: "Arimo", sans-serif; color: var(--ink); }
  .contact-row { display: flex; align-items: flex-start; gap: 10px; }
  .address { font-size: 17px; line-height: 24px; }
  .phone-row { margin-top: 14px; align-items: center; gap: 8px; font-size: 15px; }
  .phone-number { font-weight: 700; font-size: 17px; margin-right: 6px; }
</style>
</head>
<body>
<div class="canvas">
  <div class="flyer">
    <div class="hero-visual" role="img" aria-label="Hand touching glowing web interface squares on an orange background"></div>
    <svg class="flyer-shapes" width="788" height="1120" viewBox="0 0 788 1120">
      <path d="M0,495 C220,430 460,545 788,405 L788,440 C480,560 240,455 0,520 Z" fill="var(--stripe-orange)"/>
      <path d="M0,512 C220,452 470,562 788,432 L788,478 C520,570 260,475 0,552 Z" fill="var(--wave-grey)"/>
      <path d="M0,550 C260,478 520,572 788,476 L788,1120 L0,1120 Z" fill="var(--panel-light)"/>
      <path d="M0,552 C150,510 320,518 455,540 L455,965 L340,1035 L0,1035 Z" fill="var(--panel-orange)"/>
      <path d="M455,965 L788,965 L788,1120 L340,1120 L340,1035 Z" fill="var(--panel-grey)"/>
    </svg>

    <div class="abs brand-name"><span class="brand-dot"></span>Velborix</div>

    <p class="abs offer-text offer-services">We offer,<br>website design, development,<br>bespoke application</p>
    <p class="abs offer-text offer-contract">we can be hired for short term<br>contract for. companies<br>who need help with<br>then work load</p>

    <h2 class="abs section-title how-title">How It Works?</h2>
    <div class="abs step" style="top:644px"><span class="step-icon" role="img" aria-label="Pencil and brush icon"></span><span class="step-word"><small>we</small>design</span></div>
    <div class="abs step" style="top:780px"><span class="step-icon" role="img" aria-label="Tools icon"></span><span class="step-word"><small>we</small>devlop</span></div>
    <div class="abs step" style="top:918px"><span class="step-icon" role="img" aria-label="Hand truck icon"></span><span class="step-word"><small>we</small>deliver</span></div>

    <h2 class="abs section-title solutions-title">Solutions We Provide</h2>
    <ul class="abs solutions">
      <li class="solution"><span class="solution-icon" role="img" aria-label="Document icon"></span><span class="solution-name">Content Management</span></li>
      <li class="solution"><span class="solution-icon" role="img" aria-label="Globe icon"></span><span class="solution-name">Web Design</span></li>
      <li class="solution"><span class="solution-icon" role="img" aria-label="Cycle icon"></span><span class="solution-name">Bespoke System</span></li>
      <li class="solution"><span class="solution-icon" role="img" aria-label="Online shop icon"></span><span class="solution-name">e-commerce</span></li>
      <li class="solution"><span class="solution-icon" role="img" aria-label="Signup form icon"></span><span class="solution-name">Subscription System</span></li>
      <li class="solution"><span class="solution-icon" role="img" aria-label="Server icon"></span><span class="solution-name">Domain &amp; Hosting</span></li>
    </ul>

    <p class="abs cta">Get In Tuch Today</p>

    <div class="abs contact">
      <div class="contact-row address">
        <svg width="14" height="20" viewBox="0 0 14 20" style="margin-top:2px"><path d="M7,0 C3,0 0,3 0,7 C0,12 7,20 7,20 C7,20 14,12 14,7 C14,3 11,0 7,0 Z" fill="var(--ink)"/><circle cx="7" cy="7" r="2.6" fill="var(--panel-grey)"/></svg>
        <span>Velborix Ltd, Crest Suites,<br>Dunmoor Road, Cheltenham, GL53 4QT</span>
      </div>
      <div class="contact-row phone-row">
        <svg width="16" height="20" viewBox="0 0 16 20"><path d="M3,1 L6,1 L7,6 L5,8 C6,11 8,13 10,14 L12,12 L16,14 L15,18 C8,18 1,11 2,2 Z" fill="var(--ink)"/></svg>
        <span class="phone-number">01632 960 417</span>
        <svg width="18" height="13" viewBox="0 0 18 13"><rect width="18" height="13" fill="var(--ink)"/><path d="M0,0 L9,7 L18,0" fill="none" stroke="var(--panel-grey)" stroke-width="1.5"/></svg>
        <span>hello@velborix-example.com</span>
      </div>
    </div>
  </div>
</div>
</body>
</html>
```